Online tuition webpage design needed

Hi,
We are starting up an online tuition website for non- English speakers wishing to take an TOVAR test.

The webpage must include a place for people to enroll online in the course.
The home page must have:
• room for a logo (coming shortly, blue in colour)
• different packages of online tuition and paywick
• tool bar showing different pages
• perhaps a video, small pictures

This is my site currently:-

www.lexavotutoring.com

as you can see, I am not very sure how to create a website … The large logo is what I would like to use, but I project has not been finalized yet. Please note, I don’t like the logo being that large!

Sites that are similar to what I am doing and like the design of are:

http://www.brindacourse.com.au/fees

https://www.quorvel9x.net/index.php

http://www.lessonmasterpercival.co.uk/index.html

http://www.tamrunexamhub.com/

One thing I need is a place for student s to enroll, and if possible, I would like to use learnix to create exercises for students.
Currently, my site is using sitecraft. My preference is to use learnix for online activities. I am not sure if I can use both.
Thanks in advance

Target Market(s)

people wising to take an TOVAR test (English proficiency test)

Industry/Entity Type

Online

Colors
3276b5
0292cd

Requirements
Must have
• a place for enrollment and admin login for students
learnix
video
voxly, friendbook, chirpnet logos
Nice to have
• a booking calender
Should not have
• too much clutter. must be clean and professional looking

```html
<!DOCTYPE html>
<html lang="en">
<head>
<meta charset="utf-8">
<title>TOVAR Online Tuition</title>
<link href="https://fonts.googleapis.com/css2?family=Alegreya+Sans:ital,wght@0,400;0,500;0,700;1,400&display=swap" rel="stylesheet">
<style>
:root{
  --blue:#3276b5;
  --blue-dark:#2a66a0;
  --ink:#333;
  --muted:#555;
  --line:#d7d7d7;
  --dark:#2f2f2f;
  --red:#c0272d;
  --bg:#fff;
}
*{box-sizing:border-box;margin:0;padding:0}
html,body{width:720px;height:1200px;overflow:hidden}
body{font-family:"Alegreya Sans",sans-serif;color:var(--ink);background:var(--bg);position:relative}
.abs{position:absolute}

/* top bar */
.topbar{left:0;top:0;width:720px;height:30px;background:var(--blue);color:#fff;font-size:7.5px}
.topbar .contact{position:absolute;top:0;height:30px;display:flex;align-items:center;gap:6px}
.topbar .phone{left:62px}
.topbar .mail{left:148px}
.login{position:absolute;left:577px;top:6px;width:67px;height:18px;background:var(--dark);color:#fff;font-size:8px;display:flex;align-items:center;justify-content:center}

/* header */
.header{left:0;top:30px;width:720px;height:48px;background:#fff}
.brand{position:absolute;left:60px;top:7px;color:var(--blue);line-height:1}
.brand-name{font-size:22px;font-weight:500;letter-spacing:.5px;display:flex;align-items:center;gap:5px}
.brand-name i{display:inline-block;width:12px;height:12px;border-radius:50%;background:var(--blue)}
.brand-sub{font-size:7px;margin-left:32px;margin-top:1px}
.nav{position:absolute;right:72px;top:0;height:48px;display:flex;font-size:10px;color:var(--ink)}
.nav a{color:inherit;text-decoration:none;padding:0 7px;display:flex;align-items:center;height:48px;padding-top:10px}
.nav a.active{background:#f3f3f3;border-bottom:2px solid var(--blue)}

/* hero */
.hero{left:0;top:78px;width:720px;height:281px}
.hero-photo{position:absolute;inset:0;background:linear-gradient(90deg,#f1f2f3 0%,#e9ebed 45%,#dfe6ee 70%,#eef0f2 100%)}
.hero-title{position:absolute;left:75px;top:102px;width:205px;height:30px;background:var(--blue);color:#fff;font-size:16px;font-weight:400;padding-left:12px;display:flex;align-items:center}
.hero-sub{position:absolute;left:75px;top:132px;width:263px;height:29px;background:var(--dark);color:#fff;font-size:11px;padding-left:12px;display:flex;align-items:center}
.dots{position:absolute;left:83px;top:267px;display:flex;gap:3px}
.dots span{width:8px;height:8px;border-radius:50%;background:#333}
.dots span.on{background:var(--blue)}

/* features */
.feature{top:390px;width:172px;text-align:center}
.feature .icon{width:24px;height:24px;border-radius:50%;background:var(--blue);margin:0 auto;display:flex;align-items:center;justify-content:center}
.feature h3{font-weight:400;font-size:11.5px;margin-top:8px}
.feature p{font-size:7.8px;color:var(--muted);line-height:13px;margin-top:6px}

/* welcome */
.tab{left:75px;top:510px;width:375px;height:24px;border-bottom:1px solid #bbb}
.tab span{display:inline-block;height:24px;border:1px solid var(--line);border-left:2px solid var(--blue);border-bottom:none;background:#fff;font-size:8.5px;padding:0 13px;line-height:24px;width:95px}
.welcome{left:83px;top:546px;width:370px}
.welcome .lead{font-size:10px}
.welcome .intro{font-size:8px;margin-top:3px}
.checks{list-style:none;margin-top:9px}
.checks li{font-size:8px;display:flex;align-items:center;gap:7px;height:18px}

/* video */
.video{left:465px;top:510px;width:180px;height:122px;border:1px solid var(--line);padding:3px;background:#fff}
.video .screen{position:relative;width:100%;height:100%;background:#000}
.video .scene{position:absolute;left:7px;top:15px;right:7px;bottom:16px;background:linear-gradient(#fafafa,#e4e4e4)}
.video .play{position:absolute;left:50%;top:50%;width:22px;height:22px;margin:-11px 0 0 -11px;border:1.5px solid var(--blue);background:#fff;border-radius:50%;display:flex;align-items:center;justify-content:center}
.video .bar{position:absolute;left:4px;right:4px;bottom:3px;height:10px;display:flex;align-items:center;gap:5px;font-size:5px;color:#ccc}
.video .track{position:absolute;left:4px;right:4px;bottom:15px;height:1px;background:#555}

/* booking */
.label{font-size:11px;font-weight:400}
.book-title{left:465px;top:652px}
.calendar{left:465px;top:672px;width:180px;height:114px;border:1px solid var(--line);padding-top:10px;font-size:5.3px;text-align:center}
.calendar .month{font-size:5.8px;margin-bottom:3px}
.calendar table{margin:0 auto;border-collapse:collapse}
.calendar th,.calendar td{width:12px;height:12.5px;font-weight:400}
.calendar thead tr{border-bottom:1px solid #ddd}
.calendar tbody tr{border-bottom:1px solid #eee}

/* testimonials */
.testi-title{left:75px;top:680px}
.arrows{left:425px;top:684px;display:flex;gap:2px}
.arrows span{width:9px;height:9px;display:flex;align-items:center;justify-content:center}
.testimonials{left:75px;top:698px;width:375px;height:88px;border:1px solid #bbb;border-top:1px solid #999;padding:14px 16px;text-align:center;font-style:italic;font-size:8.2px;color:var(--muted);line-height:13px}
.testimonials p+p{margin-top:13px}

/* packages */
.pack-title{left:75px;top:798px}
.card{top:819px;width:180px;height:193px;background:#fff;box-shadow:0 0 4px rgba(0,0,0,.12);text-align:center}
.card .price{color:var(--blue);font-size:42px;line-height:1;margin-top:22px;font-weight:400}
.card .price sup{font-size:18px;vertical-align:top;position:relative;top:2px;margin-right:1px}
.card h4{font-size:18px;font-weight:400;margin-top:16px}
.card p{font-size:7.8px;color:var(--muted);line-height:13px;margin:16px 14px 0}
.card .pay{display:inline-block;margin-top:10px;font-size:9px;font-weight:700;color:var(--blue-dark)}

/* enrol */
.enrol{left:75px;top:1024px;width:570px;height:44px;box-shadow:0 0 4px rgba(0,0,0,.12);background:#fff}
.enrol span{position:absolute;left:15px;top:0;line-height:44px;font-size:12.5px}
.enrol a{position:absolute;right:12px;top:9px;width:101px;height:27px;background:var(--blue);color:#fff;text-decoration:none;font-size:12px;display:flex;align-items:center;justify-content:center}

/* footer */
.footer{left:0;top:1080px;width:720px;height:120px;background:var(--blue);color:#fff}
.fcol{position:absolute;top:10px}
.fcol h5{font-size:17.5px;font-weight:400;line-height:1}
.fcol p,.fcol li{font-size:7.2px;line-height:13.3px}
.fcol ul{list-style:none;margin-top:5px}
.quick p{margin-top:5px;line-height:9px}
.field{width:114px;height:13px;background:#fff;color:#666;font-size:5px;padding-left:6px;line-height:13px;margin-top:6px}
.submit{width:34px;height:11px;background:var(--red);font-size:5px;text-align:center;line-height:11px;margin-top:6px}
.social{display:flex;gap:2px;margin-top:6px}
.social span{width:10px;height:10px;border-radius:50%;background:#fff}
.address .key{margin-top:5px}
</style>
</head>
<body>

<div class="abs topbar">
  <div class="contact phone">
    <svg width="12" height="12" viewBox="0 0 24 24"><path fill="#e4533a" d="M6.6 10.8a15 15 0 0 0 6.6 6.6l2.2-2.2c.3-.3.7-.4 1-.2 1.1.4 2.3.6 3.6.6.6 0 1 .4 1 1V20c0 .6-.4 1-1 1A17 17 0 0 1 3 4c0-.6.4-1 1-1h3.5c.6 0 1 .4 1 1 0 1.3.2 2.5.6 3.6.1.3 0 .7-.2 1z"/></svg>
    <span>(+01) 555 014 2280</span>
  </div>
  <div class="contact mail">
    <svg width="20" height="12" viewBox="0 0 20 12"><rect width="20" height="12" fill="#f6b233"/><path d="M0 0l10 7 10-7" fill="none" stroke="#fff" stroke-width="1.2"/></svg>
    <span>hello@corvantagroup.com</span>
  </div>
  <div class="login">Login</div>
</div>

<header class="abs header">
  <div class="brand">
    <div class="brand-name"><i></i>TOVAR</div>
    <div class="brand-sub">Online Tuition</div>
  </div>
  <nav class="nav">
    <a href="#">Home</a>
    <a href="#" class="active">Tutorial Packages</a>
    <a href="#">Weekly Tips</a>
    <a href="#">Reading</a>
    <a href="#">Speaking</a>
    <a href="#">Listening</a>
    <a href="#">Writing</a>
    <a href="#">Contact</a>
  </nav>
</header>

<section class="abs hero">
  <div class="hero-photo" role="img" aria-label="Photo of a smiling young man in a light blue shirt holding an open laptop, on a pale city background"></div>
  <h1 class="hero-title">TOVAR Online Tuition</h1>
  <p class="hero-sub">Professional Help for People Taking an TOVAR Test</p>
  <div class="dots"><span class="on"></span><span></span><span></span></div>
</section>

<section class="abs feature" style="left:80px">
  <div class="icon"><svg width="11" height="11" viewBox="0 0 12 12"><rect x="2" y="2" width="8" height="6" fill="none" stroke="#fff"/><path d="M1 10h10" stroke="#fff"/></svg></div>
  <h3>Learn Online</h3>
  <p>You can learn anything online, you can learn to read, to write and to speak also.<br>The TOVAR provides you best online learning plat-form which is purely student oriented.</p>
</section>
<section class="abs feature" style="left:274px">
  <div class="icon"><svg width="11" height="11" viewBox="0 0 12 12"><circle cx="6" cy="4" r="2.3" fill="none" stroke="#fff"/><path d="M2 11c0-2.5 2-4 4-4s4 1.5 4 4z" fill="none" stroke="#fff"/></svg></div>
  <h3>Talk to our experts</h3>
  <p>You can learn anything online, you can learn to read, to write and to speak also.<br>The TOVAR provides you best online learning plat-form which is purely student oriented.</p>
</section>
<section class="abs feature" style="left:469px">
  <div class="icon"><svg width="11" height="11" viewBox="0 0 12 12"><rect x="1" y="2" width="7" height="5" fill="none" stroke="#fff"/><rect x="4" y="5" width="7" height="5" fill="var(--blue)" stroke="#fff"/></svg></div>
  <h3>Communicate with People</h3>
  <p>You can learn anything online, you can learn to read, to write and to speak also.<br>The TOVAR provides you best online learning plat-form which is purely student oriented.</p>
</section>

<div class="abs tab"><span>Welcome to TOVAR</span></div>
<section class="abs welcome">
  <p class="lead">We put our customer first. We listen to you and help you find what you need.</p>
  <p class="intro">If you want help in passing an TOVAR test, we can help you with:</p>
  <ul class="checks">
    <li><svg width="10" height="8" viewBox="0 0 10 8"><path d="M1 4l3 3 5-6" fill="none" stroke="var(--blue)" stroke-width="1.8"/></svg>Lessons in reading, writing, listening and speaking</li>
    <li><svg width="10" height="8" viewBox="0 0 10 8"><path d="M1 4l3 3 5-6" fill="none" stroke="var(--blue)" stroke-width="1.8"/></svg>Professional teacher feedback and tips.</li>
    <li><svg width="10" height="8" viewBox="0 0 10 8"><path d="M1 4l3 3 5-6" fill="none" stroke="var(--blue)" stroke-width="1.8"/></svg>Voxly and practice with native speakers.</li>
    <li><svg width="10" height="8" viewBox="0 0 10 8"><path d="M1 4l3 3 5-6" fill="none" stroke="var(--blue)" stroke-width="1.8"/></svg>Quick Turnaround.</li>
    <li><svg width="10" height="8" viewBox="0 0 10 8"><path d="M1 4l3 3 5-6" fill="none" stroke="var(--blue)" stroke-width="1.8"/></svg>Friendly and Approachable teachers.</li>
  </ul>
</section>

<div class="abs video">
  <div class="screen">
    <div class="scene" role="img" aria-label="Video still of a presenter in a dark suit speaking to camera"></div>
    <div class="play"><svg width="8" height="9" viewBox="0 0 8 9"><path d="M1 0l7 4.5L1 9z" fill="var(--blue)"/></svg></div>
    <div class="track"></div>
    <div class="bar">
      <svg width="6" height="6" viewBox="0 0 6 6"><path d="M0 0l6 3-6 3z" fill="#bbb"/></svg>
      <span>0:00 / 1:30</span>
    </div>
  </div>
</div>

<h2 class="abs label book-title">Book your seat</h2>
<div class="abs calendar">
  <div class="month">JANUARY 2014</div>
  <table>
    <thead><tr><th>M</th><th>T</th><th>W</th><th>T</th><th>F</th><th>S</th><th>S</th></tr></thead>
    <tbody>
      <tr><td></td><td></td><td>1</td><td>2</td><td>3</td><td>4</td><td>5</td></tr>
      <tr><td>6</td><td>7</td><td>8</td><td>9</td><td>10</td><td>11</td><td>12</td></tr>
      <tr><td>13</td><td>14</td><td>15</td><td>16</td><td>17</td><td>18</td><td>19</td></tr>
      <tr><td>20</td><td>21</td><td>22</td><td>23</td><td>24</td><td>25</td><td>26</td></tr>
      <tr><td>27</td><td>28</td><td>29</td><td>30</td><td>31</td><td></td><td></td></tr>
    </tbody>
  </table>
</div>

<h2 class="abs label testi-title">Testimonials</h2>
<div class="abs arrows">
  <span style="background:var(--dark)"><svg width="7" height="7" viewBox="0 0 7 7"><path d="M6 3.5H1M3.5 1L1 3.5 3.5 6" fill="none" stroke="#fff"/></svg></span>
  <span style="background:var(--blue)"><svg width="7" height="7" viewBox="0 0 7 7"><path d="M1 3.5h5M3.5 1L6 3.5 3.5 6" fill="none" stroke="#fff"/></svg></span>
</div>
<div class="abs testimonials">
  <p>"The process for us was made extrememly easy given their intimate knowledge and understanding of the entire Regional Efficiency Rebate Scheme and what is required for compliance."</p>
  <p>"Our dealings with the company was smooth and seamless right from the quoting process through the complicated path of compliance paperwork to implementation and wrap-up."</p>
</div>

<h2 class="abs label pack-title">Course Packages</h2>
<div class="abs card" style="left:75px">
  <div class="price"><sup>$</sup>49</div>
  <h4>Silver</h4>
  <p>Last minute TOVAR preparation.<br>Ideal for those who need to get familiar with test format and strategies.</p>
  <span class="pay">paywick</span>
</div>
<div class="abs card" style="left:270px">
  <div class="price"><sup>$</sup>99</div>
  <h4>Gold</h4>
  <p>Ideal for those who want to improve their English skills and get familiar with the test format and strategies.</p>
  <span class="pay">paywick</span>
</div>
<div class="abs card" style="left:465px">
  <div class="price"><sup>$</sup>299</div>
  <h4>Diamond</h4>
  <p>Ideal for those who want to improve their English skills, get familiar with the test and receive personalised assessment.</p>
  <span class="pay">paywick</span>
</div>

<div class="abs enrol">
  <span>Improve your TOVAR score!</span>
  <a href="#">Enrol Now</a>
</div>

<footer class="abs footer">
  <div class="fcol quick" style="left:76px">
    <h5>Quick Contact</h5>
    <p>Submit and get the quick answer<br>for your solution.</p>
    <div class="field">Name</div>
    <div class="field">E-mail</div>
    <div class="submit">Submit</div>
  </div>
  <div class="fcol" style="left:256px">
    <h5>Quick Links</h5>
    <ul><li>About</li><li>Tutorial Packages</li><li>Weekly Tips</li><li>Reading</li><li>Writing</li><li>Speaking</li></ul>
  </div>
  <div class="fcol" style="left:392px">
    <h5>Support Links</h5>
    <ul><li>Privacy</li><li>Legal</li><li>Copyright</li><li>Terms</li></ul>
    <div class="social"><span></span><span></span><span></span><span></span><span></span></div>
  </div>
  <div class="fcol address" style="left:545px">
    <h5>Contact Us</h5>
    <p class="key">ADDRESS :</p>
    <p>27, Marlow Lane. North Fenby.<br>Carradale, KS 60914, USA</p>
    <p class="key">TELEPHONE :</p>
    <p>+1 (555) 019-47-62</p>
  </div>
</footer>

</body>
</html>
```